Card design for orthopaedic surgeons working as The Brightwater Joint Centre

Business cards, letterhead

Colors

Designer to choose colors to be used in the design.

Requirements
Must have
• Late addition.
• Cards letterhead must have logos of
• Crestmoor Lindell College of Surgeons
• Varenwood Bone Health Association
Nice to have
• Back of card to have space for appointment time to be added by hand and some blank space for writing incidental other notes.

```html
<!DOCTYPE html>
<html lang="en">
<head>
<meta charset="UTF-8">
<title>The Brightwater Joint Centre – Business Card</title>
<link href="https://fonts.googleapis.com/css2?family=Montserrat:wght@400&family=Roboto:wght@400;500&display=swap" rel="stylesheet">
<style>
  :root {
    --page-bg: #e6e6e6;
    --card-white: #ffffff;
    --navy: #133e56;
    --sky: #4ba8de;
    --ink: #2f3a44;
    --rule: #5d6f7c;
  }
  * { box-sizing: border-box; margin: 0; padding: 0; }
  html, body {
    width: 1125px;
    height: 1200px;
    overflow: hidden;
    background: var(--page-bg);
  }
  .canvas {
    position: relative;
    width: 1125px;
    height: 1200px;
  }
  .card {
    position: absolute;
    left: 150px;
    width: 825px;
    height: 472px;
    border-radius: 24px;
    overflow: hidden;
    box-shadow: 0 2px 6px rgba(0,0,0,0.25);
  }
  .card--front { top: 98px; background: var(--card-white); }
  .card--back { top: 631px; background: var(--navy); }

  .brand-name {
    font-family: "Montserrat", sans-serif;
    font-weight: 400;
    white-space: nowrap;
    letter-spacing: -0.2px;
  }
  .card--front .brand-name {
    position: absolute;
    left: 58px;
    top: 84px;
    font-size: 26.5px;
    color: var(--navy);
  }
  .card--back .brand-name {
    position: absolute;
    left: 0;
    right: 0;
    top: 232px;
    text-align: center;
    font-size: 36px;
    color: #ffffff;
  }

  .holder {
    position: absolute;
    right: 64px;
    top: 258px;
    text-align: right;
    font-family: "Roboto", sans-serif;
  }
  .holder__name {
    font-size: 32px;
    font-weight: 500;
    color: var(--sky);
    line-height: 1.1;
  }
  .holder__role {
    font-size: 19px;
    color: var(--ink);
    margin-top: 4px;
  }
  .divider {
    position: absolute;
    left: 63px;
    right: 64px;
    top: 325px;
    height: 2px;
    background: var(--rule);
  }

  .contacts {
    position: absolute;
    left: 60px;
    top: 357px;
    list-style: none;
    font-family: "Roboto", sans-serif;
    font-size: 19.5px;
    color: var(--ink);
  }
  .contacts li {
    display: flex;
    align-items: center;
    height: 24px;
  }
  .contacts svg {
    width: 14px;
    height: 14px;
    margin-right: 10px;
    fill: var(--sky);
  }
  .contacts .accent { color: var(--sky); }

  .address {
    position: absolute;
    right: 64px;
    top: 366px;
    text-align: right;
    font-family: "Roboto", sans-serif;
    font-size: 19.5px;
    line-height: 24px;
    color: var(--ink);
  }

  .edge-band {
    position: absolute;
    bottom: 0;
    height: 13px;
  }
  .edge-band--dark { left: 0; width: 283px; background: var(--navy); }
  .edge-band--light { left: 288px; right: 0; background: var(--sky); }
</style>
</head>
<body>
<div class="canvas">

  <section class="card card--front">
    <div class="brand-name">The Brightwater Joint Centre</div>

    <div class="holder">
      <div class="holder__name">John Smith</div>
      <div class="holder__role">Manager</div>
    </div>

    <div class="divider"></div>

    <ul class="contacts">
      <li>
        <svg viewBox="0 0 16 16" aria-hidden="true"><path d="M3.6 1.2l2.3 2.6c.4.4.4 1 0 1.4L4.7 6.4c.9 2 2.6 3.8 4.7 4.8l1.2-1.2c.4-.4 1-.4 1.4 0l2.6 2.3c.4.4.4 1 0 1.4l-1.3 1.3c-.6.6-1.5.8-2.3.5C6 13.8 2.2 10 .5 4.9.2 4.100.4 3.2 1 2.6L2.2 1.2c.4-.4 1-.4 1.4 0z"/></svg>
        123-456-2100
      </li>
      <li>
        <svg viewBox="0 0 16 16" aria-hidden="true"><path d="M1 3h14v10H1z M1.8 3.6L8 8.6l6.2-5" stroke="#fff" stroke-width="1.2"/></svg>
        youremail@brightwatermail.com
      </li>
      <li>
        <svg viewBox="0 0 16 16" aria-hidden="true"><circle cx="8" cy="8" r="7"/><path d="M1.5 8h13M8 1.2c-2.4 2-2.4 11.6 0 13.6M8 1.2c2.4 2 2.4 11.6 0 13.6" stroke="#fff" stroke-width="1" fill="none"/></svg>
        <span>www.<span class="accent">yourwebsite</span>.com</span>
      </li>
    </ul>

    <div class="address">
      Your address<br>
      city, state, ZIP 0000
    </div>

    <div class="edge-band edge-band--dark"></div>
    <div class="edge-band edge-band--light"></div>
  </section>

  <section class="card card--back">
    <div class="brand-name">The Brightwater Joint Centre</div>
  </section>

</div>
</body>
</html>
```